Coral Slumber Depot Website

Need a design for a local Miami mattress store.
The store is called Coral Slumber Depot.
need it to be something that customers can find on the internet and will
give them my location, they need to know i have the same brand mattress as the other store except i have them at almost half the price.

the office phone number is (786)413-9067
the office address is: 24517 sw Heron Glade Ln, Miami FL 33189

included is the logo, id like to stick the with white and teal design

here are is an excerpt that can or cannot be included

"We are a premium mattress discount outlet store located in South Florida; offering Free Delivery to Broward Miami-Dade, the Keys, and Palm Beach.

We carry the best brands in the market: Kellard DreamLoft; Brodin SpineEase, Whitcombe & Lyle, Pardue, among others.

We are open 7 days a week, and we are accessible from all major highways. We are a family business and our goal is to provide you with the most comfortable and best quality mattress at a price that has no competition. Come visit us and take a look at our large inventory selection."

```html
<!DOCTYPE html>
<html lang="en">
<head>
<meta charset="utf-8">
<title>Coral Slumber Depot</title>
<link href="https://fonts.googleapis.com/css2?family=Josefin+Slab:wght@400;600&family=Montserrat:wght@500;700&family=Open+Sans:wght@400;600&family=Arimo:wght@400&display=swap" rel="stylesheet">
<style>
:root{
  --teal:#1fb3c9;
  --teal-dark:#0e8ea3;
  --teal-deep:#0a6f80;
  --teal-soft:#8ad7e3;
  --ink:#3a3a3a;
  --grey:#6b6b6b;
  --panel:#efefef;
  --line:#d8d8d8;
  --footer:#3e3e3e;
  --white:#ffffff;
}
*{margin:0;padding:0;box-sizing:border-box}
html,body{width:889px;height:1200px;overflow:hidden;background:var(--white)}
body{position:relative;font-family:"Arimo",Arial,sans-serif;color:var(--ink)}
.abs{position:absolute}
.side-band{top:130px;width:74px;height:190px;background:linear-gradient(180deg,var(--teal-deep) 0%,var(--teal) 50%,var(--teal-soft) 100%)}
.side-left{left:0}
.side-right{left:815px}
.brand-name{left:74px;top:34px;width:240px;font-family:"Josefin Slab",serif;font-weight:600;font-size:24px;color:var(--ink);letter-spacing:.5px;line-height:1}
.brand-sub{left:74px;top:62px;width:220px;font-family:"Josefin Slab",serif;font-weight:600;font-size:12px;letter-spacing:9px;color:var(--ink);padding-left:4px}
.header-phone{left:690px;top:45px;font-family:"Open Sans",sans-serif;font-size:15px;color:#9a9a9a;display:flex;align-items:center;gap:5px}
.main-nav{left:427px;top:80px;display:flex;gap:19px;font-family:"Open Sans",sans-serif;font-size:9.5px;color:#333}
.hero{left:74px;top:110px;width:741px;height:286px;border:2px solid var(--teal);background:linear-gradient(180deg,#8fb6d9 0%,#a9c6e2 30%,#eceae4 45%,#f4f2ee 80%,#b9845b 100%)}
.hero-caption{left:514px;top:330px;width:298px;height:43px;background:var(--teal);color:var(--white);font-size:18px;padding:10px 0 0 10px;font-family:"Arimo",sans-serif}
.brands{left:74px;top:412px;width:741px;height:127px;background:var(--panel);border:1px solid var(--line);border-radius:4px}
.brand-tile{top:436px;width:152px;height:77px;border:3px solid var(--white);display:flex;align-items:center;justify-content:center;text-align:center;font-family:"Open Sans",sans-serif;font-weight:600;font-size:14px;line-height:1.2}
.tile-a{left:113px;background:#b8102d;color:var(--white)}
.tile-b{left:281px;background:#e9f3fb;color:#1f3f8a}
.tile-c{left:452px;background:#f2d9a6;color:#3b2a12}
.tile-d{left:622px;background:#c9c9c9;color:#4a4a4a}
.arrow{top:459px;width:18px;height:26px}
.map-card{left:74px;top:582px;width:196px;height:259px;border:1px solid var(--line)}
.map{left:80px;top:586px;width:183px;height:92px;background:linear-gradient(135deg,#e8e5dc,#f3edc9 50%,#dfe3d8)}
.addr-label{left:80px;top:689px;width:183px;height:22px;background:var(--teal);color:var(--white);font-family:"Montserrat",sans-serif;font-weight:700;font-size:14px;padding:3px 0 0 3px}
.addr{left:81px;top:724px;font-size:13px;line-height:15px;color:#333}
.spot{left:74px;top:790px;width:74px;height:23px;background:#444;color:var(--white);font-size:12px;padding:4px 0 0 8px}
.hours{left:74px;top:865px;width:199px;height:178px;background:var(--panel)}
.hours h3{position:absolute;left:18px;top:14px;font-family:"Montserrat",sans-serif;font-weight:700;font-size:17.5px;color:var(--teal)}
.hours-row{position:absolute;left:0;width:199px;height:20px;display:flex;align-items:center;font-family:"Montserrat",sans-serif;font-weight:500;font-size:11px;color:#555}
.hours-row span:nth-child(1){width:94px;padding-left:12px}
.hours-row span:nth-child(2){width:46px}
.row-white{background:var(--white)}
.open{left:86px;top:983px;width:168px;height:50px;border:1px solid #bbb;background:#f7f7f7}
.open-line1{left:136px;top:994px;font-family:"Montserrat",sans-serif;font-size:12.5px;color:#777}
.open-line2{left:125px;top:1010px;font-family:"Montserrat",sans-serif;font-weight:700;font-size:13.5px;color:#444}
.intro{left:306px;top:585px;width:512px;font-family:"Josefin Slab",serif;font-weight:600;font-size:15px;line-height:17.5px;letter-spacing:.6px;color:var(--teal)}
.body-copy{left:306px;top:652px;width:506px;font-family:"Arimo",sans-serif;font-size:8.8px;line-height:16.3px;color:#555}
.body-copy p+p{margin-top:3px}
.lead{left:306px;top:838px;width:508px;font-size:12.7px;line-height:15px;color:#333}
.rule{left:306px;top:886px;width:508px;height:1px;background:#e4e4e4}
.promo{left:307px;top:896px;width:320px;font-family:"Open Sans",sans-serif;font-size:8.5px;color:#333}
.promo-title{font-weight:600}
.promo-sub{color:#8b1a1a;margin-top:12px}
.promo ul{list-style:none;margin-top:12px}
.promo li{position:relative;padding-left:26px;line-height:15px}
.promo li::before{content:"";position:absolute;left:13px;top:5px;border-left:4px solid var(--teal);border-top:3px solid transparent;border-bottom:3px solid transparent}
.promo .inline-phone{font-size:14px;color:#aaa}
.promo-call{margin-top:14px;font-weight:600;font-size:9.5px}
.support{left:632px;top:898px;width:182px;height:144px;border:1px solid var(--line);background:linear-gradient(180deg,#f6f6f6,#e8e8e8)}
.support-photo{left:640px;top:905px;width:95px;height:110px;background:linear-gradient(180deg,#e6c7a5,#f1e4d6);border-radius:6px}
.support-badge{left:737px;top:930px;width:70px;height:70px;border-radius:50%;background:#f0b81e;border:4px solid #222}
.support-number{left:632px;top:1017px;width:182px;height:25px;background:#f4f4f4;font-family:"Arimo",sans-serif;font-size:20px;color:#111;text-align:center;letter-spacing:.5px;padding-top:1px}
.site-footer{left:0;top:1097px;width:889px;height:103px;background:var(--footer);border-top:2px solid #2c2c2c}
.footer-links{left:93px;top:1113px;display:flex;gap:17px;font-family:"Open Sans",sans-serif;font-size:8px;color:#cfcfcf}
.footer-links .sep{color:#aaa}
.follow{left:93px;top:1140px;font-family:"Open Sans",sans-serif;font-size:12.5px;color:#cfcfcf}
.social{top:1159px;width:20px;height:20px;border-radius:50%;background:#d9d9d9}
.footer-text{left:233px;top:1147px;font-family:"Open Sans",sans-serif;font-size:8.6px;color:#e0e0e0;letter-spacing:.2px}
</style>
</head>
<body>

<div class="abs side-band side-left" role="img" aria-label="Teal decorative side band"></div>
<div class="abs side-band side-right" role="img" aria-label="Teal decorative side band"></div>

<header>
  <div class="abs brand-name">Coral Slumber Depot</div>
  <div class="abs brand-sub">OUTLET</div>
  <div class="abs header-phone">
    <svg width="13" height="12" viewBox="0 0 13 12" aria-hidden="true"><path d="M1 4 C1 1 12 1 12 4 L10 5 L9 3 L4 3 L3 5Z M3 6 H10 L11 11 H2Z" fill="#1fb3c9"/></svg>
    <span>(786)413-9067</span>
  </div>
  <nav class="abs main-nav">
    <span>HOME</span><span>WE ARE MATTRESS</span><span>DISCOUNTERS</span><span>LOCATION</span><span>GET IN TOUCH</span>
  </nav>
</header>

<div class="abs hero" role="img" aria-label="Photo of a white quilted mattress with pillows in a blue bedroom"></div>
<div class="abs hero-caption">Lorem Ipsum is simply dummy</div>

<section class="abs brands"></section>
<svg class="abs arrow" style="left:67px" viewBox="0 0 18 26" aria-hidden="true"><path d="M18 0 H6 Q0 0 0 13 Q0 26 6 26 H18Z" fill="#7a7a7a"/><path d="M12 7 L6 13 L12 19" stroke="#fff" stroke-width="2.5" fill="none"/></svg>
<div class="abs brand-tile tile-a">Kellard DreamLoft</div>
<div class="abs brand-tile tile-b">Brodin SpineEase</div>
<div class="abs brand-tile tile-c">Whitcombe &amp; Lyle</div>
<div class="abs brand-tile tile-d">Pardue</div>
<svg class="abs arrow" style="left:804px" viewBox="0 0 18 26" aria-hidden="true"><path d="M0 0 H12 Q18 0 18 13 Q18 26 12 26 H0Z" fill="#7a7a7a"/><path d="M6 7 L12 13 L6 19" stroke="#fff" stroke-width="2.5" fill="none"/></svg>

<aside>
  <div class="abs map-card"></div>
  <div class="abs map" role="img" aria-label="Street map showing the store location with a pin"></div>
  <div class="abs addr-label">THE OFFICE ADDRESS:</div>
  <div class="abs addr">24517 sw Heron Glade Ln<br>&nbsp;Miami FL 33189<br><span style="display:block;margin-top:5px">&nbsp;Tel: (786)413-9067</span></div>
  <div class="abs spot">Spot Us ››</div>

  <div class="abs hours">
    <h3>STORE HOURS:</h3>
    <div class="hours-row" style="top:45px"><span>MON -  WED</span><span>10.00</span><span>18.00</span></div>
    <div class="hours-row row-white" style="top:65px"><span>THURS - FRI</span><span>10.00</span><span>19.00</span></div>
    <div class="hours-row" style="top:86px"><span>SAT</span><span>10.00</span><span>18.00</span></div>
  </div>
  <div class="abs open"></div>
  <svg class="abs" style="left:94px;top:988px" width="36" height="30" viewBox="0 0 36 30" aria-hidden="true"><path d="M0 28 C8 12 20 4 34 0 C24 8 18 16 14 28Z" fill="#1fb3c9"/></svg>
  <div class="abs open-line1">WE ARE OPEN</div>
  <div class="abs open-line2">7 DAYS A WEEK</div>
</aside>

<main>
  <h1 class="abs intro">WE ARE A FAMILY BUSINESS AND OUR GOAL IS TO PROVIDE YOU WITH THE MOST COMFORTABLE AND BEST QUALITY MATTRESS AT A PRICE THAT HAS NO COMPETITION</h1>
  <div class="abs body-copy">
    <p>Based in Linden Park, Texas, we design, provide, and service licensed and unlicensed, point-to-point and point-to-multipoint microwave systems. For over 40 years, Northgate Signal Works has built and delivered mission critical microwave communi-cations productsLorem Ipsum is simply dummy text of the printing and typesetting industry. Lorem Ipsum has been the industry's standard dummy text ever since the 1500s, when an unknown printer took a galley of type and scrambled it to make a type specimen book. It has survived not only five centuries, but also the leap into electronic typesetting, remaining essentially unchanged.</p>
    <p>Lorem Ipsum is simply dummy text of the printing and typesetting industry. Lorem Ipsum has been the industry's standard dummy text ever since the 1500s, when an unknown printer took a galley of type and scrambled it to make a type speci-men book. It has survived not only five centuries, but also the leap into electronic typesetting, remaining essentially unchanged. It was popularised in the 1960s with the release of Marlow Transfer sheets containing Lorem Ipsum passages, and more recently with desktop publishing software like Quillset Layout including versions of Lorem Ipsum.</p>
  </div>
  <p class="abs lead">We are a premium mattress discount outlet store located in South Florida; offering Free Delivery to Broward Miami-Dade, the Keys, and Palm Beach</p>
  <div class="abs rule"></div>

  <div class="abs promo">
    <div class="promo-title">Lorem Ipsum is simply dummy text of the printing .....</div>
    <div class="promo-sub">It has survived not only five centuries :</div>
    <ul>
      <li>The standard chunk of Lorem Ipsum used.</li>
      <li>There are many variations of passages of lorem.</li>
      <li>All the Lorem Ipsum generators on the Internet.</li>
      <li>The generated Lorem Ipsum is therefore always free.</li>
      <li>Small Guy Hits It Big!<span class="inline-phone">(786)413-9067</span></li>
    </ul>
    <div class="promo-call">Call  NOW on (786)413-9067. We will exceed your expectations.</div>
  </div>

  <div class="abs support"></div>
  <div class="abs support-photo" role="img" aria-label="Photo of a customer support agent with a headset"></div>
  <div class="abs support-badge" role="img" aria-label="Round gold support badge"></div>
  <div class="abs support-number">02.61.38.74.05</div>
</main>

<footer class="abs site-footer"></footer>
<nav class="abs footer-links">
  <span>About Us</span><span class="sep">~</span><span>Categories</span><span class="sep">~</span><span>FAQ's</span><span class="sep">~</span><span>General Conditions of Sale online</span><span class="sep">~</span><span>Shopping Cart</span><span class="sep">~</span><span>Our Partners</span><span class="sep">~</span><span>Contact Us</span><span class="sep">~</span><span>Sitemap</span>
</nav>
<div class="abs follow">Follow Us on:</div>
<div class="abs social" style="left:94px" role="img" aria-label="Social network link"></div>
<div class="abs social" style="left:122px" role="img" aria-label="Social network link"></div>
<div class="abs social" style="left:151px" role="img" aria-label="Social network link"></div>
<div class="abs footer-text">Lorem Ipsum is simply dummy text of the printing and typesetting industry. Lorem Ipsum has been the industry's standard dummy text</div>

</body>
</html>
```